Veldmark Supplies Business Card

Professional business card that stand out to our potential customers. Front and back with clean modern design

Industry/Entity Type

Oil and gas

Contact Information for Business Card

Name, address, website , office phone and cell number

Requirements
Must have
• Editable files for each employee

```html
<!DOCTYPE html>
<html lang="en">
<head>
<meta charset="utf-8">
<title>Veldmark Supplies Business Card</title>
<link rel="stylesheet" href="https://fonts.googleapis.com/css2?family=Poppins:wght@400;500;700;800&display=swap">
<style>
  :root {
    --backdrop: #d9d9db;
    --card: #262628;
    --card-deep: #1a1a1b;
    --pattern-light: #4a4a4c;
    --red: #e8202a;
    --blue: #12aee0;
    --white: #ffffff;
    --rule: #8a8a8c;
  }
  * { margin: 0; padding: 0; box-sizing: border-box; }
  html, body {
    width: 1200px; height: 900px; overflow: hidden;
    background: var(--backdrop);
    font-family: "Poppins", sans-serif;
  }
  .canvas { position: relative; width: 1200px; height: 900px; }

  .card {
    position: absolute;
    left: 320px;
    width: 560px; height: 320px;
    border-radius: 18px;
    overflow: hidden;
    background: var(--card);
    box-shadow: 0 10px 30px rgba(0,0,0,.25);
  }
  .card-back { top: 110px; }
  .card-front { top: 470px; }

  /* back */
  .back-pattern {
    position: absolute; inset: 0;
    background: linear-gradient(150deg, var(--pattern-light) 0%, #2c2c2e 50%, var(--card-deep) 100%);
  }
  .back-mark {
    position: absolute; right: 150px; bottom: 60px;
    display: flex; align-items: center; gap: 8px;
    color: var(--red); font-weight: 700; font-size: 15px;
  }
  .back-mark .dot { width: 12px; height: 12px; background: var(--red); }

  /* front */
  .brand {
    position: absolute; left: 40px; top: 126px;
    width: 240px;
    display: flex; align-items: center; gap: 10px;
    color: var(--white); font-weight: 700; font-size: 18px;
    text-transform: uppercase; letter-spacing: .3px;
    white-space: nowrap;
  }
  .brand .square { width: 20px; height: 20px; background: var(--red); flex: none; }

  .divider {
    position: absolute; left: 300px; top: 58px;
    width: 1px; height: 180px; background: var(--rule);
  }

  .details { position: absolute; left: 322px; top: 58px; color: var(--white); }
  .person-name { color: var(--red); font-weight: 800; font-size: 24px; line-height: 1.1; }
  .person-title { font-size: 13px; margin-bottom: 10px; }
  .address { font-size: 13px; line-height: 1.35; margin-bottom: 8px; }
  .contact-list { list-style: none; font-size: 13px; line-height: 1.6; }
  .contact-list li { display: flex; align-items: center; gap: 8px; }
  .contact-list svg { width: 11px; height: 11px; fill: var(--red); flex: none; }

  .edge-band { position: absolute; left: 0; bottom: 0; width: 100%; height: 22px; }
</style>
</head>
<body>
<main class="canvas">

  <section class="card card-back" aria-label="Card back">
    <div class="back-pattern" role="img" aria-label="Repeating glossy monogram pattern on black, fading from grey to black"></div>
    <div class="back-mark"><span class="dot"></span>Veldmark Supplies</div>
  </section>

  <section class="card card-front" aria-label="Card front">
    <div class="brand"><span class="square"></span>Veldmark Supplies</div>

    <div class="divider"></div>

    <div class="details">
      <p class="person-name">Marlo Keane</p>
      <p class="person-title">President</p>
      <p class="address">412 N.Larkfield Suite 7<br>Midland, Tx 79701</p>
      <ul class="contact-list">
        <li>
          <svg viewBox="0 0 12 12" aria-hidden="true"><path d="M2 1h3l1 3-1.5 1a6 6 0 0 0 2.5 2.5L8 6l3 1v3a1 1 0 0 1-1 1A9 9 0 0 1 1 2a1 1 0 0 1 1-1z"/></svg>
          (555)204-1187
        </li>
        <li>
          <svg viewBox="0 0 12 12" aria-hidden="true"><path d="M3 0h6a1 1 0 0 1 1 1v10a1 1 0 0 1-1 1H3a1 1 0 0 1-1-1V1a1 1 0 0 1 1-1zm0 2v7h6V2z"/></svg>
          (555)204-1188
        </li>
        <li>
          <svg viewBox="0 0 12 12" aria-hidden="true"><path d="M0 2h12v1L6 7 0 3zM0 4.5l6 4 6-4V10H0z"/></svg>
          sales@veldmarksupplies.com
        </li>
        <li>
          <svg viewBox="0 0 12 12" aria-hidden="true"><circle cx="6" cy="6" r="6"/></svg>
          www.veldmarksupplies.com
        </li>
      </ul>
    </div>

    <svg class="edge-band" viewBox="0 0 560 22" preserveAspectRatio="none" aria-hidden="true">
      <polygon points="0,0 300,0 290,22 0,22" fill="var(--red)"/>
      <polygon points="306,0 560,0 560,22 296,22" fill="var(--blue)"/>
    </svg>
  </section>

</main>
</body>
</html>
```